Banner Pop Up Opt In Form REDESIGNS - SLEEK BLACK LOOK

Please redesign banners attached.

I am looking for a very sleek look....I do not like this collage of images on these current designs. Please keep all content same but use images that pop.

I have an acccount at www.pixvane-example.com or you can use your own images.

I like black background for somereason because it looks very sleek....but these designs should pop , build trust and credibility and have easy opt in form....SLEEK AND MODERN LOOK is what im looking for....

Target Market(s)

Consumers on websites

Requirements
Must have
• Please redesign banners attached.

Nice to have

Should not have

```html
<!DOCTYPE html>
<html lang="en">
<head>
<meta charset="UTF-8">
<title>Resort Offer Opt-In Banner</title>
<link rel="stylesheet" href="https://fonts.googleapis.com/css2?family=Arimo:wght@400;700&family=Poppins:wght@400&display=swap">
<style>
  :root {
    --headline-green: #1ee85c;
    --offer-gold: #f6b60a;
    --text-white: #ffffff;
    --panel-shade: rgba(8, 8, 8, 0.72);
    --field-bg: #ffffff;
    --field-border: #c9c9c9;
    --field-text: #1a1a1a;
    --submit-blue: #0a45e3;
    --submit-edge: #06308f;
    --sky-top: #3d3a44;
    --sky-mid: #9a7a78;
    --sky-glow: #d9a986;
    --sea: #4e4446;
    --shore-dark: #151313;
  }
  * { box-sizing: border-box; margin: 0; padding: 0; }
  html, body {
    width: 1200px;
    height: 1032px;
    overflow: hidden;
    background: #000;
  }
  .banner {
    position: relative;
    width: 1200px;
    height: 1032px;
    overflow: hidden;
    font-family: "Arimo", Arial, sans-serif;
    color: var(--text-white);
  }
  .beach-photo {
    position: absolute;
    inset: 0;
    background:
      radial-gradient(ellipse 420px 260px at 860px 470px, rgba(230, 180, 140, 0.55), transparent 70%),
      linear-gradient(180deg,
        var(--sky-top) 0%,
        var(--sky-mid) 22%,
        var(--sky-glow) 40%,
        var(--sky-mid) 52%,
        var(--sea) 60%,
        var(--shore-dark) 72%,
        #2a2325 86%,
        #3a3438 100%);
  }
  .form-panel {
    position: absolute;
    left: 0;
    top: 0;
    width: 578px;
    height: 1032px;
    background: var(--panel-shade);
  }
  .headline {
    position: absolute;
    left: 32px;
    top: 24px;
    font-weight: 700;
    font-size: 59px;
    line-height: 74px;
    color: var(--headline-green);
    letter-spacing: 0.5px;
  }
  .intro {
    position: absolute;
    left: 32px;
    top: 186px;
    font-weight: 700;
    font-size: 23.5px;
    line-height: 30px;
    text-transform: uppercase;
  }
  .offer {
    position: absolute;
    left: 32px;
    top: 258px;
    font-weight: 700;
    font-size: 29px;
    line-height: 38px;
    color: var(--offer-gold);
  }
  .optin-form {
    position: absolute;
    left: 32px;
    top: 366px;
    width: 438px;
  }
  .field {
    height: 61px;
    margin-bottom: 8px;
    background: var(--field-bg);
    border: 1px solid var(--field-border);
    border-radius: 7px;
    padding-left: 21px;
    display: flex;
    align-items: center;
    font-family: "Poppins", Arial, sans-serif;
    font-size: 25px;
    color: var(--field-text);
  }
  .submit-button {
    margin-top: 1px;
    height: 77px;
    background: var(--submit-blue);
    border-bottom: 3px solid var(--submit-edge);
    border-radius: 6px;
    display: flex;
    align-items: center;
    justify-content: center;
    font-family: "Poppins", Arial, sans-serif;
    font-size: 31px;
    color: var(--text-white);
    letter-spacing: 0.5px;
  }
  .redeem-note {
    position: absolute;
    left: 32px;
    top: 952px;
    font-size: 23.5px;
    line-height: 30px;
  }
</style>
</head>
<body>
  <div class="banner">
    <div class="beach-photo" role="img" aria-label="Photo of a thatched beach hut and palm trees silhouetted against a tropical sunset, reflected in a pool"></div>
    <div class="form-panel"></div>

    <h1 class="headline">WANT A<br>GREAT OFER ?</h1>
    <p class="intro">Souscribe to our email list<br>and recive a complimentry</p>
    <p class="offer">7 NIGHTS RESORTS/CONDO -<br>3500 + LOCATIONS</p>

    <div class="optin-form">
      <div class="field">Name</div>
      <div class="field">Email</div>
      <div class="field">Phone</div>
      <div class="submit-button">SUBMIT</div>
    </div>

    <p class="redeem-note">We will send an email and a text message with<br>the offer and instractions on how to redeem.</p>
  </div>
</body>
</html>
```